BOLD & MINIMALIST DESIGN NEEDED

We want a very bold but minimalistic business card design that is impactful and utilizes both sides of the business card. Our current logo is included for your use.

We want bold fonts and good use of negative space. We don't want the logo to overpower the design.

Target Market(s)

Professionals who are building new commercial buildings.

Industry/Entity Type

Construction

Contact Information for Business Card

Name, Title, email, office phone, cell phone, website

Font styles to use
Serif
Sans Serif

Requirements
Must have
• Bold design!

```html
<!DOCTYPE html>
<html lang="en">
<head>
<meta charset="utf-8">
<title>Kestrel Build – Business Card</title>
<link rel="stylesheet" href="https://fonts.googleapis.com/css2?family=Poppins:wght@400;500;700&display=swap">
<style>
  :root {
    --page-bg: #2a2a2a;
    --card-bg: #262626;
    --card-back-bg: #242424;
    --brand-green: #77ad2c;
    --text-white: #f2f2f2;
    --text-muted: #c9c9c9;
    --mark-grey: #5a5a5a;
    --ink-dark: #1b1b1b;
  }
  * { margin: 0; padding: 0; box-sizing: border-box; }
  html, body {
    width: 1200px; height: 576px; overflow: hidden;
    background: var(--page-bg);
    font-family: "Poppins", sans-serif;
  }
  .stage { position: relative; width: 1200px; height: 576px; }
  .card {
    position: absolute; top: 138px;
    width: 484px; height: 294px;
    border-radius: 8px; overflow: hidden;
  }
  .card--front { left: 102px; background: var(--card-bg); }
  .card--back { left: 596px; width: 481px; background: var(--card-back-bg); }

  /* front */
  .front-brand {
    position: absolute; left: 0; right: 0; top: 96px;
    display: flex; align-items: center; justify-content: center; gap: 14px;
  }
  .front-brand__square { width: 34px; height: 34px; background: var(--mark-grey); }
  .front-brand__name {
    font-weight: 700; font-size: 54px; line-height: 1;
    color: var(--mark-grey); letter-spacing: 2px;
  }
  .front-url {
    position: absolute; left: 0; right: 0; top: 252px;
    text-align: center; font-size: 13px; letter-spacing: 6.5px;
    color: var(--text-muted);
  }

  /* back */
  .back-brand {
    position: absolute; left: 26px; top: 34px;
    font-weight: 700; font-size: 34px; line-height: 1;
    color: var(--text-white); letter-spacing: 1px;
  }
  .name-band {
    position: absolute; left: 0; top: 124px;
    width: 284px; height: 69px;
    background: var(--brand-green);
    padding: 18px 0 0 25px;
  }
  .name-band__name { font-size: 19px; font-weight: 500; color: var(--ink-dark); line-height: 1.1; }
  .name-band__title { font-size: 11px; color: var(--ink-dark); margin-top: 4px; }
  .contact-list {
    position: absolute; left: 26px; top: 219px; list-style: none;
  }
  .contact-list li {
    display: flex; align-items: center; gap: 9px;
    font-size: 12px; color: var(--text-white); height: 17px;
  }
  .contact-list svg { width: 10px; height: 10px; fill: var(--brand-green); }
  .ground-curve { position: absolute; left: 0; top: 0; }
</style>
</head>
<body>
<main class="stage">
  <section class="card card--front" aria-label="Card front">
    <div class="front-brand">
      <span class="front-brand__square"></span>
      <span class="front-brand__name">KESTREL</span>
    </div>
    <p class="front-url">www.kestrelbuild.com</p>
  </section>

  <section class="card card--back" aria-label="Card back">
    <p class="back-brand">KESTREL BUILD</p>
    <div class="name-band">
      <p class="name-band__name">Daniel Ortiz</p>
      <p class="name-band__title">Director</p>
    </div>
    <ul class="contact-list">
      <li><svg viewBox="0 0 10 10"><path d="M1 3 Q5 0 9 3 L8 4.5 L6.5 3.5 L3.5 3.5 L2 4.5 Z M2.5 5 H7.5 L8.5 9 H1.5 Z"/></svg>555-014-2200</li>
      <li><svg viewBox="0 0 10 10"><path d="M0.5 2 H9.5 V8 H0.5 Z" /><path d="M0.5 2 L5 5.5 L9.5 2" fill="none" stroke="#242424" stroke-width="1"/></svg>daniel@kestrelbuild.com</li>
      <li><svg viewBox="0 0 10 10"><circle cx="5" cy="5" r="4.5"/><path d="M0.5 5 H9.5 M5 0.5 V9.5" stroke="#242424" stroke-width="0.8"/></svg>www.kestrelbuild.com</li>
    </ul>
    <svg class="ground-curve" width="481" height="294" viewBox="0 0 481 294" aria-hidden="true">
      <path d="M188 294 Q300 250 481 244 V294 Z" fill="var(--text-white)"/>
    </svg>
  </section>
</main>
</body>
</html>
```